Brisk Fixwell business card

I need business card for my business, I think you have all my details.six months ago I design with you car wrap design. We would like to design both side of the card. On front of card we would like logo , Name and our contact details.
At the back we are looking to mentioned our services.
The name will be:
Faridoullan Mestor
Managing Director
Ph:07952338417
Email:info@brisk-fixwell.com
Web:www.brisk-fixwell.com
So we have our logo, you don’t need to change the logo.
Please see the attachment.
Thanks

Target Market(s)

Home improvement

Industry/Entity Type

Home Improvement

Contact Information for Business Card

Company name: Brisk Fixwell
Name: Faridoullan Mestor
Position: Director
Ph:07952338417
Web: www.brisk-fixwell.com
Add: 42 Corvale Road
Hounslow
TW3 9KD
SECOND PERSON
Nizamuddel mestor
Position: Handyman
Ph: 07812 564037
Email: info@brisk-fixwell.com
Add: 18 Brackwin Lane Road
Hounslow
TW6 2LB

```html
<!DOCTYPE html>
<html lang="en">
<head>
<meta charset="utf-8">
<title>Brisk Fixwell – Business Card</title>
<link href="https://fonts.googleapis.com/css2?family=Arimo:wght@400;700&display=swap" rel="stylesheet">
<style>
  :root {
    --navy: #263a8a;
    --navy-deep: #1f2f78;
    --red: #e31f2d;
    --grey: #a3a3a6;
    --ink: #2a2a2a;
    --paper: #ffffff;
    --stage: #e9e9eb;
  }
  * { box-sizing: border-box; margin: 0; padding: 0; }
  html, body { width: 1200px; height: 1015px; overflow: hidden; }
  body {
    background: var(--stage);
    font-family: "Arimo", Arial, sans-serif;
    display: flex; flex-direction: column; align-items: center; justify-content: center;
    gap: 22px;
  }
  .card {
    position: relative; width: 840px; height: 480px; overflow: hidden;
    box-shadow: 0 8px 24px rgba(0,0,0,.18);
  }

  /* Services side */
  .card--services { background: var(--navy); color: var(--paper); }
  .services__pattern {
    position: absolute; inset: 0;
    background: radial-gradient(ellipse at 50% 40%, #2d45a0 0%, var(--navy) 55%, var(--navy-deep) 100%);
  }
  .services__brand {
    position: absolute; top: 150px; left: 0; right: 0;
    display: flex; align-items: center; justify-content: center; gap: 14px;
  }
  .brand-name { font-weight: 700; letter-spacing: .5px; }
  .services__brand .brand-name { font-size: 40px; color: var(--paper); }
  .brand-dot { width: 16px; height: 16px; background: var(--red); border-radius: 50%; }
  .services__list {
    position: absolute; left: 70px; right: 50px; bottom: 70px;
    display: grid; grid-template-columns: 1fr 1fr 1fr 1fr 1.7fr;
    row-gap: 10px; column-gap: 18px; list-style: none;
  }
  .services__list li { font-size: 22px; white-space: nowrap; display: flex; align-items: center; gap: 8px; }
  .services__list li::before {
    content: ""; width: 9px; height: 9px; border-radius: 50%; background: var(--red); flex: none;
  }

  /* Contact side */
  .card--contact { background: var(--paper); }
  .contact__mark {
    position: absolute; left: 90px; top: 95px; width: 250px; height: 250px;
    background: var(--navy);
  }
  .contact__divider {
    position: absolute; left: 400px; top: 30px; width: 1px; height: 330px;
    background: linear-gradient(to bottom, rgba(0,0,0,0), rgba(0,0,0,.12), rgba(0,0,0,0));
  }
  .contact__body { position: absolute; left: 450px; top: 62px; right: 30px; }
  .contact__body .brand-name { font-size: 44px; color: var(--navy); display: block; margin-bottom: 34px; }
  .person__name { font-size: 24px; font-weight: 700; color: var(--navy); letter-spacing: .5px; }
  .person__role { font-size: 17px; color: #555; letter-spacing: 1px; margin: 2px 0 16px; }
  .contact__lines { list-style: none; }
  .contact__lines li {
    display: flex; align-items: center; gap: 12px; font-size: 20px; color: var(--ink); margin-bottom: 6px;
  }
  .contact__lines svg { width: 20px; height: 20px; flex: none; fill: var(--navy); }
  .web-domain { color: var(--navy); }
  .contact__address { font-size: 20px; color: var(--ink); line-height: 1.3; margin-top: 14px; }

  .band { position: absolute; bottom: 0; }
  .band--grey { left: 0; width: 320px; height: 12px; background: var(--grey); }
  .band--red { left: 326px; width: 250px; height: 22px; background: var(--red); }
  .band--navy { left: 582px; right: 0; height: 22px; background: var(--navy); }
</style>
</head>
<body>

  <section class="card card--services">
    <div class="services__pattern" role="img" aria-label="Repeating brand-mark pattern in tonal blues"></div>
    <div class="services__brand">
      <span class="brand-name">Brisk Fixwell</span>
      <span class="brand-dot"></span>
    </div>
    <ul class="services__list">
      <li>Plumbing</li>
      <li>Decking</li>
      <li>Gutter</li>
      <li>Plastering</li>
      <li>Painting &amp; Decorating</li>
      <li>Carpentry</li>
      <li>Fence</li>
      <li>Flooring</li>
      <li>Tilling</li>
      <li>Gardening</li>
    </ul>
  </section>

  <section class="card card--contact">
    <div class="contact__mark" role="img" aria-label="Brisk Fixwell brand mark"></div>
    <div class="contact__divider"></div>
    <div class="contact__body">
      <span class="brand-name">Brisk Fixwell</span>
      <p class="person__name">FARIDOULLAN MESTOR</p>
      <p class="person__role">DIRECTOR</p>
      <ul class="contact__lines">
        <li>
          <svg viewBox="0 0 24 24" aria-hidden="true"><path d="M6.6 10.8a15.1 15.1 0 0 0 6.6 6.6l2.2-2.2a1 1 0 0 1 1-.25 11.4 11.4 0 0 0 3.6.57 1 1 0 0 1 1 1V20a1 1 0 0 1-1 1A17 17 0 0 1 3 4a1 1 0 0 1 1-1h3.5a1 1 0 0 1 1 1c0 1.25.2 2.45.57 3.57a1 1 0 0 1-.25 1z"/></svg>
          07952338417
        </li>
        <li>
          <svg viewBox="0 0 24 24" aria-hidden="true"><path d="M2 5h20v14H2z M3.5 6.5 12 13l8.5-6.5" fill="none" stroke="#263a8a" stroke-width="2"/></svg>
          info@brisk-fixwell.com
        </li>
        <li>
          <svg viewBox="0 0 24 24" aria-hidden="true"><g fill="none" stroke="#263a8a" stroke-width="1.8"><circle cx="12" cy="12" r="9.5"/><ellipse cx="12" cy="12" rx="4.2" ry="9.5"/><path d="M2.5 12h19M4 7h16M4 17h16"/></g></svg>
          <span>www.<span class="web-domain">brisk-fixwell</span>.com</span>
        </li>
      </ul>
      <p class="contact__address">42 Corvale Road<br>Hounslow, TW3 9KD</p>
    </div>
    <div class="band band--grey"></div>
    <div class="band band--red"></div>
    <div class="band band--navy"></div>
  </section>

</body>
</html>
```